New Website for World Wide Charity (KOLVAN)

We need a dynamic web design for our brand new charity organisation that will be working worldwide. We will be funded by donations so need to attract people to donate.

What We Do
We work to optimise the wellbeing of the planet, the animals and all that live within. Our slogan is Achieving Vibrational Equilibrium.

We have included a Powerpoint document which may help you understand what we need, it is just an idea for structure and style, it is not set in stone so feel free to be as creative as you like!
Updates

Designs look the same

Target Market(s)

Adults 18+ with an interest in animal, environmental. Businesses that may like to support our natural world or already support our natural world.

Number of Pages Required

3 page

Colors

Designer to choose colors to be used in the design.

Requirements
Must have
• We need the website to be easy to use and understand.

Web pages will be Home, What We Do, Who We Are, Success Stories, What You Can Do (Blog section), Seek Help, Donate, Join.
Nice to have
• Natural feel, easy to navigate, Ideally the website will look natural and organic.

Natural colours, blues, greens, sand, gold, brown, grey, silver, Orange and yellow for impact.
Should not have
• Should not have a dark coloured theme.

```html
<!DOCTYPE html>
<html lang="en">
<head>
<meta charset="utf-8">
<title>KOLVAN – Achieving Vibrational Equilibrium</title>
<link href="https://fonts.googleapis.com/css2?family=Roboto+Condensed:wght@700&family=Poppins:wght@400;500;600&display=swap" rel="stylesheet">
<style>
:root{
  --blue:#2c4a94;
  --blue-dark:#223a78;
  --green:#3aa37a;
  --ink:#2b2b2b;
  --muted:#6d6d6d;
  --pale-blue:#eef3fb;
  --pale-grey:#f1f1f1;
  --white:#ffffff;
}
*{box-sizing:border-box;margin:0;padding:0}
html,body{width:1200px;height:3444px;overflow:hidden;background:var(--white)}
body{font-family:"Poppins",sans-serif;color:var(--ink);position:relative}
.abs{position:absolute}
.head{font-family:"Roboto Condensed",sans-serif;font-weight:700;text-transform:uppercase}

/* hero */
.hero{left:0;top:0;width:1200px;height:860px;background:linear-gradient(180deg,#cfc9bd 0%,#e4ded3 35%,#b9b4a6 65%,#6f7a64 100%)}
.topbar{left:0;top:0;width:1200px;height:30px;background:var(--blue);color:#fff;font-size:12px;display:flex;justify-content:flex-end;align-items:center;gap:26px;padding-right:60px}
.topbar .social{display:flex;gap:10px}
.topbar .social span{width:12px;height:12px;border-radius:50%;background:#fff;opacity:.85}
.logo{left:40px;top:12px;width:160px;height:160px;background:#fff;border:3px solid var(--blue);display:flex;flex-direction:column;align-items:center;justify-content:center;gap:10px}
.logo .dot{width:56px;height:56px;border-radius:50%;background:var(--green)}
.logo .name{font-family:"Poppins",sans-serif;font-weight:600;font-size:22px;color:var(--blue);letter-spacing:2px}
.nav{left:390px;top:56px;display:flex;align-items:center;gap:10px;font-size:13px;font-weight:500;color:var(--blue)}
.nav a{padding:8px 12px;text-decoration:none;color:var(--blue)}
.nav a.active{background:var(--blue);color:#fff}
.nav a.btn{background:var(--green);color:#fff;text-transform:uppercase;font-size:12px;padding:9px 18px}
.hero-title{left:352px;top:224px;font-size:56px;line-height:52px;color:#1e1e1e}
.hero-sub{left:352px;top:334px;font-size:28px;color:var(--green);font-family:"Roboto Condensed",sans-serif;font-weight:700}
.hero-btn{left:352px;top:396px;background:var(--blue);color:#fff;font-size:13px;font-weight:500;padding:12px 30px;text-transform:uppercase}

.card{top:560px;width:320px;height:250px}
.card .photo{width:100%;height:190px}
.card .label{height:60px;background:#fff;display:flex;flex-direction:column;align-items:center;justify-content:center;color:var(--blue);font-size:26px}
.card .label.blue{background:var(--blue);color:#fff}
.card .label small{font-family:"Poppins",sans-serif;font-size:10px;font-weight:500}

/* sections */
.band{position:absolute}
.photo{background:linear-gradient(135deg,#8a8a82,#3e3f3a)}
.feature .title{font-size:30px;color:var(--blue);position:relative}
.feature .title i{font-style:normal;position:absolute;left:100%;top:-8px;font-size:40px;color:#e9e9e9;margin-left:4px;z-index:-1}
.feature p{font-size:13px;line-height:21px;color:var(--muted);margin-top:18px;width:400px}
.more{display:inline-block;margin-top:26px;border:1px solid var(--blue);color:var(--blue);font-size:11px;padding:7px 18px}

/* blogs */
.blogs-bg{left:0;top:2470px;width:1200px;height:570px;background:linear-gradient(180deg,#fff 0%,#f4f4f2 50%,#c9ccc6 100%)}
.blogs-title{left:0;width:1200px;top:2528px;text-align:center;color:var(--blue);font-size:30px}
.post-date{font-size:11px;color:var(--muted)}
.post-title{font-size:22px;font-weight:600;line-height:30px;color:var(--ink)}
.small-title{font-size:14px;font-weight:600;line-height:20px}

/* footer */
.footer{left:0;top:3032px;width:1200px;height:376px;background:var(--blue);color:#fff}
.footer .trees{left:0;top:-40px;width:1200px;height:60px}
.flogo{left:100px;top:70px;width:180px;height:180px;border-radius:50%;background:#fff;display:flex;align-items:center;justify-content:center;font-weight:600;font-size:24px;color:var(--blue);letter-spacing:2px}
.fcol{top:70px;font-size:12px;line-height:24px}
.fcol h4{font-size:15px;font-weight:600;margin-bottom:10px}
.fcol div{opacity:.85}
.copy{left:0;top:3408px;width:1200px;height:36px;background:var(--blue-dark);color:#fff;font-size:11px;display:flex;align-items:center;justify-content:space-between;padding:0 40px}
</style>
</head>
<body>

<div class="abs hero" role="img" aria-label="Misty pine forest landscape"></div>
<div class="abs topbar"><span>✉ hello@kolvan.org</span><span>☎ (555) 010-2468</span><span class="social"><span></span><span></span><span></span><span></span></span></div>
<div class="abs logo"><span class="dot"></span><span class="name">KOLVAN</span></div>
<nav class="abs nav">
  <a class="active">Home</a><a>What We Do</a><a>Who We Are</a><a>Success Stories</a><a>What You Can Do</a><a class="btn">Donate</a><a class="btn">Join</a>
</nav>
<h1 class="abs head hero-title">Help Raise<br>World Vibration</h1>
<div class="abs hero-sub">Achieving Vibrational Equilibrium</div>
<div class="abs hero-btn">Make a Difference</div>

<div class="abs card" style="left:100px"><div class="photo" role="img" aria-label="Hand touching a young plant sprout"></div><div class="label head">Environment</div></div>
<div class="abs card" style="left:440px"><div class="photo" role="img" aria-label="Person caring for a dog"></div><div class="label head">Animal</div></div>
<div class="abs card" style="left:780px"><div class="photo" role="img" aria-label="Volunteers handing out food"></div><div class="label head blue">Human<small>FIND OUT MORE</small></div></div>

<!-- environment -->
<div class="band" style="left:0;top:900px;width:560px;height:480px;background:var(--pale-blue)"></div>
<div class="band photo" style="left:100px;top:940px;width:500px;height:410px" role="img" aria-label="Finger touching a seedling growing from soil"></div>
<div class="band feature" style="left:672px;top:1000px">
  <h2 class="title head">Environment<i>TEXT</i></h2>
  <p>Lorem Ipsum is simply dummy text of the printing and typesetting industry.</p>
  <p>Lorem Ipsum has been the industry's standard dummy text ever since the 1500s, when an unknown printer took a galley of type and scrambled it to make a type specimen book.</p>
  <p>It has survived not only five centuries, but also the leap into electronic typesetting, remaining essentially unchanged.</p>
  <span class="more">Read More ›</span>
</div>

<!-- animal -->
<div class="band" style="left:1010px;top:1420px;width:190px;height:480px;background:var(--pale-grey)"></div>
<div class="band photo" style="left:600px;top:1480px;width:500px;height:400px" role="img" aria-label="Person hugging a dog"></div>
<div class="band feature" style="left:100px;top:1530px">
  <h2 class="title head">Animal</h2>
  <p>Lorem Ipsum is simply dummy text of the printing and typesetting industry.</p>
  <p>Lorem Ipsum has been the industry's standard dummy text ever since the 1500s, when an unknown printer took a galley of type and scrambled it to make a type specimen book.</p>
  <p>It has survived not only five centuries, but also the leap into electronic typesetting, remaining essentially unchanged.</p>
  <span class="more">Read More ›</span>
</div>

<!-- human -->
<div class="band" style="left:0;top:1960px;width:560px;height:470px;background:var(--pale-blue)"></div>
<div class="band" style="left:100px;top:2000px;width:500px;height:400px;background:linear-gradient(135deg,#c9b8a8,#7b8aa0)" role="img" aria-label="Masked volunteers serving a meal"></div>
<div class="band feature" style="left:672px;top:2050px">
  <h2 class="title head">Human</h2>
  <p>Lorem Ipsum is simply dummy text of the printing and typesetting industry.</p>
  <p>Lorem Ipsum has been the industry's standard dummy text ever since the 1500s, when an unknown printer took a galley of type and scrambled it to make a type specimen book.</p>
  <p>It has survived not only five centuries, but also the leap into electronic typesetting, remaining essentially unchanged.</p>
  <span class="more">Read More ›</span>
</div>

<!-- blogs -->
<div class="abs blogs-bg" role="img" aria-label="Faded misty forest backdrop"></div>
<h2 class="abs head blogs-title">Blogs</h2>
<div class="abs" style="left:100px;top:2620px;width:480px;height:240px;background:linear-gradient(135deg,#6f9a4e,#2f5a3a)" role="img" aria-label="Volunteer collecting litter in a park"></div>
<div class="abs" style="left:640px;top:2632px;width:440px">
  <div class="post-date">Blog · 12</div>
  <div class="post-title" style="margin-top:8px">Good vibes or bad vibes Which do you prefer?</div>
  <p style="font-size:12px;line-height:19px;color:var(--muted);margin-top:12px">Lorem Ipsum is simply dummy text of the printing and typesetting industry. Lorem Ipsum has been the industry's standard text.</p>
  <div class="post-date" style="margin-top:16px">▣ 08 Feb 2021</div>
  <span class="more" style="margin-top:14px">Read More ›</span>
</div>
<div class="abs" style="left:100px;top:2898px;width:180px;height:90px;background:linear-gradient(135deg,#b49a5a,#5e6b3a)" role="img" aria-label="Sunlit field"></div>
<div class="abs" style="left:300px;top:2900px;width:260px"><div class="small-title">Lorem Ipsum is simply dummy text of the printing...</div><div class="post-date" style="margin-top:8px">▣ 08 Feb 2021</div></div>
<div class="abs" style="left:615px;top:2898px;width:180px;height:90px;background:linear-gradient(135deg,#9aa6a0,#4b5954)" role="img" aria-label="People planting trees"></div>
<div class="abs" style="left:815px;top:2900px;width:265px"><div class="small-title">Lorem Ipsum is simply dummy text of the printing...</div><div class="post-date" style="margin-top:8px">▣ 08 Feb 2021</div></div>

<!-- footer -->
<footer class="abs footer">
  <svg class="abs trees" viewBox="0 0 1200 60" preserveAspectRatio="none" aria-hidden="true"><path d="M0 60 L0 40 L40 20 L80 40 L130 10 L180 38 L240 22 L300 40 L360 15 L420 38 L480 25 L540 40 L600 12 L660 36 L720 20 L780 40 L840 14 L900 38 L960 22 L1020 40 L1080 16 L1140 38 L1200 24 L1200 60 Z" fill="#2c4a94"/></svg>
  <div class="abs flogo">KOLVAN</div>
  <div class="abs fcol" style="left:340px"><h4>Quick Links</h4><div>Home</div><div>What We Do</div><div>Who We Are</div><div>Success Stories</div><div>What You Can Do</div></div>
  <div class="abs fcol" style="left:540px"><h4>Get Involved</h4><div>Join Us</div><div>Volunteer</div><div>Donate</div><div>Blog</div></div>
  <div class="abs fcol" style="left:740px"><h4>Legal</h4><div>Terms and Conditions</div><div>Cookies</div><div>Privacy Policy</div></div>
  <div class="abs fcol" style="left:940px"><h4>Contact Info</h4><div>☎ (555) 010-2468</div><div>✉ hello@kolvan.org</div><div>⌖ 12 Fernhill Road,<br>&nbsp;&nbsp;&nbsp;Lakeside, CA</div></div>
</footer>
<div class="abs copy"><span>Copyright © 2021 KOLVAN | All Rights Reserved</span><span style="display:flex;gap:10px"><span style="width:10px;height:10px;border-radius:50%;background:#fff"></span><span style="width:10px;height:10px;border-radius:50%;background:#fff"></span><span style="width:10px;height:10px;border-radius:50%;background:#fff"></span><span style="width:10px;height:10px;border-radius:50%;background:#fff"></span></span></div>

</body>
</html>
```